Stationery Design Project

Hi All,

We need you to design stationary for a new Business and Accounting Advisory Firm. We have already got the logo designed and it is attached. If you could also if possible, match the fonts in your design to that on the logo’s provided.

What we need:
- Business Card
- A4 Letter head
- A4 Folders
- PPT template (Title page and regular page)

And what ever else you want to throw in.

We are in the process of getting the web site designed, however below is a list of websites which we like which will give you an understanding of the style that we are going for.

- plivant.example
- moldrabay.example
- tarvenhook.example
- quillorbank.example

I look forward to your seeing your design.
Updates

Hi All,

I have just realised that I forgot that i need to include a Sworn Ledgerkeepers image on the letter head, please find attaced as File 1. Could you please have this image in the bottom left header.

Regards,

Marcus

Industry/Entity Type

Business

Requirements
Must have
• Outputs:
- Documents ready to print
- Generic editable information
- Pdf copies of the documents
- Word version of letterhead

```html
<!DOCTYPE html>
<html lang="en">
<head>
<meta charset="utf-8">
<title>Kellorn Partners — Business Cards</title>
<link rel="stylesheet" href="https://fonts.googleapis.com/css2?family=EB+Garamond:wght@500&family=Tinos:wght@400;700&display=swap">
<style>
  :root {
    --board: #8a8c8e;
    --paper: #ffffff;
    --brand-blue: #3a5a9c;
    --brand-deep: #34589b;
    --brand-orange: #f58a1f;
    --ink: #333333;
    --ink-strong: #111111;
    --rule: #b9b9b9;
  }
  * { margin: 0; padding: 0; box-sizing: border-box; }
  html, body { width: 1200px; height: 709px; overflow: hidden; }
  body { background: var(--board); position: relative; font-family: "Tinos", "Times New Roman", serif; color: var(--ink); }

  .card { position: absolute; width: 558px; height: 318px; background: var(--paper); overflow: hidden; }
  .card--front-centred { left: 25px; top: 19px; }
  .card--front-split   { left: 618px; top: 19px; }
  .card--back-blue     { left: 25px; top: 365px; background: var(--brand-deep); }
  .card--back-white    { left: 618px; top: 365px; }

  .base-band { position: absolute; left: 0; bottom: 0; width: 100%; height: 13px; background: var(--brand-blue); }

  .wordmark { position: absolute; left: 0; width: 100%; display: flex; justify-content: center; align-items: center; gap: 12px; }
  .wordmark__dot { width: 30px; height: 30px; border-radius: 50%; background: var(--brand-orange); }
  .wordmark__name { font-family: "EB Garamond", Georgia, serif; font-weight: 500; font-size: 34px; color: var(--brand-blue); line-height: 1; }

  .line { position: absolute; left: 0; width: 100%; text-align: center; font-size: 17px; line-height: 1; white-space: nowrap; }
  .person-name { font-weight: 700; font-size: 21px; color: var(--brand-blue); }
  .designation { font-size: 17px; }
  .contact { display: inline-flex; align-items: center; gap: 4px; }
  .contact + .contact { margin-left: 10px; }
  .contact--web { color: var(--ink-strong); }
  .icon { width: 11px; height: 11px; fill: var(--brand-blue); flex: none; }

  .split-left { position: absolute; right: 317px; top: 0; text-align: right; font-size: 17px; }
  .split-left > * { position: absolute; right: 0; white-space: nowrap; line-height: 1; }
  .split-divider { position: absolute; left: 259px; top: 177px; width: 1px; height: 104px; background: var(--rule); }
  .split-right { position: absolute; left: 272px; top: 0; font-size: 17px; }
  .split-right > .contact { position: absolute; left: 0; white-space: nowrap; line-height: 1; margin: 0; }

  .back-name { position: absolute; left: 0; width: 100%; top: 120px; text-align: center; font-family: "EB Garamond", Georgia, serif; font-weight: 500; font-size: 54px; color: #ffffff; line-height: 1; }
  .back-url { position: absolute; left: 0; width: 100%; text-align: center; font-size: 18px; letter-spacing: 1.6px; line-height: 1; }
  .back-url--light { color: #ffffff; top: 268px; }
  .back-url--dark { color: var(--ink-strong); top: 243px; font-size: 19px; }
</style>
</head>
<body>

<svg width="0" height="0" style="position:absolute">
  <symbol id="i-phone" viewBox="0 0 12 12"><path d="M3 1 L5 3.5 L4 5 C4.8 6.6 5.6 7.4 7 8 L8.5 7 L11 9 L9.5 11 C5 10.5 1.5 7 1 2.5 Z"/></symbol>
  <symbol id="i-mobile" viewBox="0 0 12 12"><path d="M2 6 L3.5 2.5 H8.5 L10 6 H11 V9.5 H9.5 V10.5 H8 V9.5 H4 V10.5 H2.5 V9.5 H1 V6 Z M3.3 6 H8.7 L7.8 3.6 H4.2 Z"/></symbol>
  <symbol id="i-mail" viewBox="0 0 12 12"><path d="M1 3 H11 V10 H1 Z M1.8 3.8 L6 7 L10.2 3.8 Z" fill-rule="evenodd"/></symbol>
  <symbol id="i-globe" viewBox="0 0 12 12"><path d="M6 1 A5 5 0 1 0 6 11 A5 5 0 1 0 6 1 Z M6 2.2 C5 3.2 4.6 4.6 4.6 6 C4.6 7.4 5 8.8 6 9.8 C7 8.8 7.4 7.4 7.4 6 C7.4 4.6 7 3.2 6 2.2 Z M2.2 5.5 H9.8 V6.5 H2.2 Z" fill-rule="evenodd"/></symbol>
</svg>

<section class="card card--front-centred">
  <div class="wordmark" style="top:58px"><span class="wordmark__dot"></span><span class="wordmark__name">Kellorn Partners</span></div>
  <p class="line" style="top:152px"><span class="person-name">Your Name,</span> <span class="designation">Designation</span></p>
  <p class="line" style="top:199px">
    <span class="contact"><svg class="icon"><use href="#i-phone"/></svg>0123-456-789</span>
    <span class="contact"><svg class="icon"><use href="#i-mobile"/></svg>0123-456-789</span>
  </p>
  <p class="line" style="top:224px">
    <span class="contact"><svg class="icon"><use href="#i-mail"/></svg>info@kellornpartners.example</span>
    <span class="contact contact--web"><svg class="icon"><use href="#i-globe"/></svg>www.kellornpartners.example</span>
  </p>
  <p class="line" style="top:267px">Street Name, City Name, State, City Zip Code</p>
  <div class="base-band"></div>
</section>

<section class="card card--front-split">
  <div class="wordmark" style="top:72px"><span class="wordmark__dot"></span><span class="wordmark__name">Kellorn Partners</span></div>
  <div class="split-left">
    <span class="person-name" style="top:181px">Your Name</span>
    <span class="designation" style="top:203px">Designation</span>
    <span style="top:234px">Street Name, City Name</span>
    <span style="top:256px">State, City Zip Code</span>
  </div>
  <div class="split-divider"></div>
  <div class="split-right">
    <span class="contact" style="top:185px"><svg class="icon"><use href="#i-phone"/></svg>0123-456-789</span>
    <span class="contact" style="top:209px"><svg class="icon"><use href="#i-mobile"/></svg>0123-456-789</span>
    <span class="contact" style="top:233px"><svg class="icon"><use href="#i-mail"/></svg>info@kellornpartners.example</span>
    <span class="contact contact--web" style="top:256px"><svg class="icon"><use href="#i-globe"/></svg>www.kellornpartners.example</span>
  </div>
  <div class="base-band"></div>
</section>

<section class="card card--back-blue">
  <p class="back-name">Kellorn Partners</p>
  <p class="back-url back-url--light">www.kellornpartners.example</p>
</section>

<section class="card card--back-white">
  <div class="wordmark" style="top:128px"><span class="wordmark__dot"></span><span class="wordmark__name">Kellorn Partners</span></div>
  <p class="back-url back-url--dark">www.kellornpartners.example</p>
</section>

</body>
</html>
```